Modern looking signage for dental office.

Exterior signage for passing cars
Updates
Need extra days to review
Target Market(s)
Cars passing by
Font styles to use
Sans Serif
Colors
3276b5
Requirements
Must have
- Logo
- OPEN ON SUTURDAY AND SUNDAY
- NIGHT CLINIC AVAILABLE
- PLEASE USE THE FONT TYPE IN FILE 4 UPLOADED BELOW.
- (847) 302-7469
- Modern looking

```html
<!DOCTYPE html>
<html lang="en">
<head>
<meta charset="utf-8">
<title>Nova Dental – Exterior Sign</title>
<link rel="stylesheet" href="https://fonts.googleapis.com/css2?family=Arimo:wght@400;500&family=Roboto+Condensed:wght@400&display=swap">
<style>
  :root {
    --page-bg: #e6e9ec;
    --sign-white: #ffffff;
    --sign-grey: #e4e4e4;
    --brand-blue: #0e5499;
    --ink-dark: #3a3433;
    --ink-tagline: #4a4443;
    --text-light: #ffffff;
  }
  * { margin: 0; padding: 0; box-sizing: border-box; }
  html, body {
    width: 1200px;
    height: 1200px;
    overflow: hidden;
    background: var(--page-bg);
  }
  .sign {
    position: absolute;
    left: 50px;
    top: 270px;
    width: 1100px;
    height: 660px;
    background: var(--sign-white);
    box-shadow: 0 10px 30px rgba(0,0,0,0.15);
    overflow: hidden;
    font-family: "Arimo", Arial, sans-serif;
  }
  .sign-shapes {
    position: absolute;
    inset: 0;
  }
  .brand {
    position: absolute;
    left: 130px;
    top: 40px;
    display: flex;
    align-items: center;
    gap: 26px;
  }
  .brand-circle {
    width: 150px;
    height: 150px;
    border-radius: 50%;
    border: 3px solid var(--ink-dark);
    background: var(--sign-white);
    flex: none;
  }
  .brand-name {
    font-family: "Arimo", Arial, sans-serif;
    font-weight: 400;
    font-size: 92px;
    letter-spacing: 2px;
    color: var(--ink-dark);
    white-space: nowrap;
  }
  .tagline {
    position: absolute;
    left: 370px;
    top: 212px;
    font-family: "Roboto Condensed", "Arial Narrow", sans-serif;
    font-size: 46px;
    color: var(--ink-tagline);
    letter-spacing: 0.5px;
    white-space: nowrap;
  }
  .night-clinic {
    position: absolute;
    left: 38px;
    top: 322px;
    font-size: 46px;
    line-height: 62px;
    color: var(--brand-blue);
    letter-spacing: 1px;
  }
  .weekend {
    position: absolute;
    right: 38px;
    top: 318px;
    text-align: right;
    color: var(--text-light);
    font-size: 52px;
    line-height: 64px;
    letter-spacing: 2px;
    white-space: nowrap;
  }
  .phone {
    position: absolute;
    right: 38px;
    top: 530px;
    display: flex;
    align-items: center;
    gap: 26px;
    color: var(--text-light);
    font-size: 62px;
    font-weight: 500;
    letter-spacing: 3px;
    white-space: nowrap;
  }
  .phone-icon { width: 60px; height: 60px; flex: none; }
</style>
</head>
<body>
  <div class="sign">
    <svg class="sign-shapes" width="1100" height="660" viewBox="0 0 1100 660" aria-hidden="true">
      <defs>
        <linearGradient id="panel-shade" x1="0" y1="0" x2="1" y2="0">
          <stop offset="0" stop-color="#dcdcdc"/>
          <stop offset="1" stop-color="#f4f4f4"/>
        </linearGradient>
      </defs>
      <polygon points="0,0 220,0 470,660 0,660" fill="url(#panel-shade)"/>
      <polygon class="band-weekend" points="280,290 1100,290 1100,470 350,470" fill="var(--brand-blue)"/>
      <polygon class="band-phone" points="370,505 1100,505 1100,660 430,660" fill="var(--brand-blue)"/>
    </svg>

    <div class="brand">
      <span class="brand-circle"></span>
      <span class="brand-name">NOVA DENTAL</span>
    </div>
    <div class="tagline">MODERN GENERAL DENTISTRY</div>

    <div class="night-clinic">NIGHT<br>CLINIC<br>AVAILABLE</div>

    <div class="weekend">OPEN ON<br>SATURDAY AND SUNDAY</div>

    <div class="phone">
      <svg class="phone-icon" viewBox="0 0 60 60" aria-hidden="true">
        <circle cx="30" cy="30" r="27" fill="none" stroke="#fff" stroke-width="4"/>
        <path d="M22 15c2-1 4 0 5 2l2 5c1 2 0 3-1 4l-2 2c1 3 4 6 7 8l2-2c1-1 3-2 4-1l5 2c2 1 3 3 2 5l-1 2c-2 3-6 3-10 1-7-4-13-10-16-17-2-4-1-9 3-11z" fill="#fff"/>
      </svg>
      <span>(847) 302-7469</span>
    </div>
  </div>
</body>
</html>
```